Start-Up für Training, Coaching & Consulting sucht modernes Webdesign!
Zielgruppe
Wer ist TAVI Training, Coaching & Consulting?
Wir führen Führungskräftetrainings durch, machen Privatkunden für Bewerbungen fit und unterstützen Unternehmen mit Verkaufstrainings. Wir entwickeln Persönlichkeiten im Coaching. Wir beraten Unternehmen und helfen ihnen dabei, ihre Geschäftsabläufe und Prozesse zu optimieren. Dabei steht unsere hohe Qualität im Mittelpunkt - gemeinsam mit unseren kreativen Trainingsmethoden. Unser Background (Diplom-Kaufleute und geprüfte Trainer) bietet dafür die passende Ausgangslage.
Was bedeutet TAVI?
Tavi ist Maori und bdeutet Kreis/Spirale. Er symbolisiert einen wachsenden Silberfarn und steht für persönliche Entwicklung und Entfaltung. Der Tavi ist einerseits unser Namensgeber und unser Logo, andererseits steht der Tavi aber auch für unsere Werte: Denn wir wollen unseren Kunden dabei helfen zu wachsen und sich weiterzuentwickeln - und dies auf eine hochqualitative und seriöse Art und Weise ohne den Eindruck von Esoterik oder Erlebnispädagogik zu vermitteln.
Aufgabenstellung
Modernes Design, das unsere Philosophie widerspiegelt: Wir möchten unseren Kunden auf seriöse und hochqualitative Weise weiterentwickeln. Wir stehen für nachhaltigen Lernerfolg, kreative Trainingsmethoden, Abwechslung, Spaß am Lernen, Qualität, Kompetenz, Fachwissen und Dynamik.
Layout:
1) Header: QMSR geprüfter Trainer, Menüpunkte (siehe Architektur)
2) Banner
3) 3 Teaser (Training, Coaching, Consulting) + Header + 2-3 Zeilen Text (+Icons)
>>> Sichtbarer Bereich auf Homepage: Menü, Banner, Teaser
4) "Warum Sie uns wählen sollten": 5 bullet points ohne weiteren Text
5) "Aus unserem Blog": Frame für 3 Blogartikel + Bild + Datum + Header + 2-3 Zeilen Text
6) Alle drei QMSR Logos
7) Footer: Click Us (quick links), Contact Us (Adresse), Follow Us (Pinnwald, ZOLP, Kontaktor)
8) Copyright + Impressum
>>> Das Design soll klar sein, aber nicht zu kantig. Vielmehr sollen abgerundete Ecken und dynamische Elemente genutzt werden.
Architektur:
3 Ebenen:
1) Homepage
2) TAVI, Training, Coaching, Consulting, für Trainer, Kundenstimmen/Referenzen, Kontakt
3) noch zu bestimmende Produktdetailseiten
Texte werden noch erstellt, Layout kann ggf. mit Platzhaltertext gefüllt werden.
Bildmaterial: Logo und vorhandenes Imagebild werden zur Verfügung gestellt. Bilder können ggf. gekauft werden. Vorschläge erwünscht.
Corporate colors:
grün: #a2c61b + monochromatic colors
http://www.tintoskop.de/a2c61b
grau: #474747 + monochromatic colors
http://www.tintoskop.de/474747

```html
<!DOCTYPE html>
<html lang="en">
<head>
<meta charset="utf-8">
<title>TAVI Training, Coaching &amp; Consulting</title>
<link href="https://fonts.googleapis.com/css2?family=Lato:ital,wght@0,300;0,400;0,700;1,400&display=swap" rel="stylesheet">
<style>
:root{
  --green:#a2c61b;
  --grey-800:#2f2f2f;
  --grey-700:#3a3a3a;
  --grey-600:#474747;
  --grey-400:#8a8a8a;
  --grey-200:#e8e8e8;
  --grey-100:#f4f4f4;
  --white:#ffffff;
}
*{box-sizing:border-box;margin:0;padding:0}
html,body{width:1200px;height:879px;overflow:hidden;background:var(--white)}
body{font-family:'Lato',sans-serif;color:var(--grey-600);position:relative}
a{text-decoration:none;color:inherit}

.topbar{position:absolute;left:0;top:0;width:1200px;height:19px;background:var(--grey-700);color:#cfcfcf;font-size:8px}
.topbar .contact{position:absolute;left:244px;top:5px;display:flex;gap:6px;align-items:center}
.topbar .sep{width:1px;height:9px;background:#666}
.topbar .lang{position:absolute;left:917px;top:5px}
.icon{fill:var(--green)}

.header{position:absolute;left:0;top:19px;width:1200px;height:62px;background:var(--grey-800)}
.brand{position:absolute;left:244px;top:10px;color:var(--white)}
.brand-name{display:flex;align-items:center;gap:5px;font-size:26px;font-weight:700;letter-spacing:1px;line-height:1}
.brand-dot{width:14px;height:14px;border-radius:50%;background:var(--green)}
.brand-tag{font-size:5.5px;color:#ddd;margin-top:5px;letter-spacing:.2px}
.social-top{position:absolute;left:911px;top:12px;display:flex;gap:4px}
.social-top span{width:12px;height:12px;border:1px solid #cfcfcf;border-radius:2px;font-size:7px;color:#cfcfcf;display:flex;align-items:center;justify-content:center}
.nav{position:absolute;left:456px;top:41px;display:flex;font-size:10px;font-weight:400;color:var(--white)}
.nav a{padding:0 13px 11px;position:relative}
.nav a.active{color:var(--green)}
.nav a.active::after{content:"";position:absolute;left:0;right:0;bottom:0;height:2px;background:var(--green)}
.nav a:last-child{padding-right:0}

.hero{position:absolute;left:0;top:81px;width:1200px;height:238px;
  background:radial-gradient(ellipse at 38% 40%,#7fc23a 0%,#3f8d1e 30%,transparent 55%),
  radial-gradient(ellipse at 80% 45%,#6fb52e 0%,#2f7a17 35%,transparent 60%),
  linear-gradient(100deg,#1e4a10 0%,#2f6a17 40%,#2b5f14 70%,#1d4a0f 100%)}
.hero-text{position:absolute;left:253px;top:67px;color:var(--white)}
.hero h1{font-size:23px;font-weight:400;color:var(--green);line-height:1}
.hero p{font-size:11px;line-height:14px;margin-top:10px;width:330px}
.btn{display:inline-block;background:var(--green);color:var(--white);text-align:center}
.hero .btn{margin-top:12px;width:147px;height:28px;line-height:28px;font-size:12px}

.teasers{position:absolute;left:0;top:319px;width:1200px;height:280px}
.card{position:absolute;top:38px;width:199px;height:210px;background:var(--grey-100);box-shadow:0 1px 3px rgba(0,0,0,.22)}
.card-media{height:105px}
.card h2{font-size:15px;font-weight:300;color:var(--grey-600);margin:8px 10px 0;letter-spacing:.3px}
.card p{font-size:9px;line-height:14px;font-weight:300;color:var(--grey-400);margin:6px 10px 0}
.card .more{display:block;margin:8px 10px 0;font-size:11px;font-weight:300;color:var(--green)}
.card .more::after{content:" \25B8";font-size:7px;color:var(--green)}
.m-training{background:linear-gradient(135deg,#cfd6de,#9aa9b9 55%,#eef0f2)}
.m-coaching{background:linear-gradient(135deg,#d9d2c9,#4a5566 55%,#c9d0d8)}
.m-consulting{background:linear-gradient(90deg,#b7cbd8,#8ea6b6 60%,#3a3f47)}

.badges{position:absolute;left:0;top:599px;width:1200px;height:84px;background:var(--grey-100);border-top:1px solid var(--grey-200)}
.badge{position:absolute}

.footer{position:absolute;left:0;top:683px;width:1200px;height:196px;background:var(--grey-800);color:#d4d4d4}
.footer h3{position:absolute;top:33px;font-size:11px;font-weight:400;color:var(--white)}
.links{position:absolute;left:252px;top:56px;list-style:none;font-size:9.5px}
.links li{height:19.4px}
.links li::before{content:"\25B8";font-size:6px;margin-right:7px;color:#bbb}
.links li.active{color:var(--green)}
.address{position:absolute;left:395px;top:57px;font-size:9.5px;line-height:13.5px}
.address div{display:flex;gap:6px;margin-bottom:8px}
.address svg{fill:#bbb;flex:none;margin-top:2px}
.field{position:absolute;background:var(--grey-700);border:1px solid #555;font-size:8px;font-style:italic;color:#cfcfcf;padding:4px 7px}
.send{position:absolute;left:664px;top:109px;width:124px;height:18px;line-height:18px;font-size:9.5px}
.follow{position:absolute;left:861px;top:60px;display:flex;gap:7px;font-size:9px;font-weight:700;color:var(--white);white-space:nowrap}
.foot-brand{position:absolute;left:861px;top:92px;color:#8a8a8a}
.foot-brand .brand-name{font-size:24px}
.foot-brand .brand-dot{background:#6a6a6a}
.foot-brand .brand-tag{color:#8a8a8a}
.copyright{position:absolute;left:244px;top:174px;width:712px;border-top:1px solid #555;font-size:8px;padding:5px 0 0 8px}
</style>
</head>
<body>

<div class="topbar">
  <div class="contact">
    <svg width="7" height="8" viewBox="0 0 10 10"><path class="icon" d="M2 0l2 2-1 2c1 1.5 2 2.5 3 3l2-1 2 2-2 2C4 10 0 6 0 2z"/></svg>
    <span>12 4411 902</span><span class="sep"></span>
    <svg width="8" height="6" viewBox="0 0 10 7"><path class="icon" d="M0 0h10v7H0zM0 0l5 4 5-4"/></svg>
    <span>hallo@tavi-studio.de</span>
  </div>
  <div class="lang">English &nbsp;▾</div>
</div>

<header class="header">
  <div class="brand">
    <div class="brand-name">TAVI<span class="brand-dot"></span></div>
    <div class="brand-tag">Training • Coaching • Consulting</div>
  </div>
  <div class="social-top" aria-label="Pinnwald, ZOLP, Kontaktor"><span>P</span><span>Z</span><span>K</span></div>
  <nav class="nav">
    <a class="active" href="#">HOME</a><a href="#">ABOUT US</a><a href="#">TRAINING</a><a href="#">COACHING</a><a href="#">CONSULTANT</a><a href="#">JOBS</a><a href="#">CONTACT US</a>
  </nav>
</header>

<section class="hero" role="img" aria-label="Close-up of an unfurling green fern frond">
  <div class="hero-text">
    <h1>WELCOME TEXT</h1>
    <p>Lorem Ipsum is simply dummy text of the printing and typesetting industry. Lorem Ipsum has been the industry's standard.</p>
    <a class="btn" href="#">CONTACT US</a>
  </div>
</section>

<section class="teasers">
  <article class="card" style="left:282px">
    <div class="card-media m-training" role="img" aria-label="Trainer presenting at a flipchart to a seated group"></div>
    <h2>TRAINING</h2>
    <p>Lorem Ipsum is simply dummy text of the printing and typesetting industry. Lorem Ipsum has been the industry's standard</p>
    <a class="more" href="#">Read More</a>
  </article>
  <article class="card" style="left:501px">
    <div class="card-media m-coaching" role="img" aria-label="Business team talking around a table"></div>
    <h2>COACHING</h2>
    <p>Lorem Ipsum is simply dummy text of the printing and typesetting industry. Lorem Ipsum has been the industry's standard</p>
    <a class="more" href="#">Read More</a>
  </article>
  <article class="card" style="left:720px">
    <div class="card-media m-consulting" role="img" aria-label="Consultant in suit beside a bright meeting room"></div>
    <h2>CONSULTING</h2>
    <p>Lorem Ipsum is simply dummy text of the printing and typesetting industry. Lorem Ipsum has been the industry's standard</p>
    <a class="more" href="#">Read More</a>
  </article>
</section>

<section class="badges" aria-label="QMSR memberships and certificates">
  <div class="badge" style="left:392px;top:24px;width:24px;height:31px;background:#1560b8"></div>
  <div class="badge" style="left:537px;top:24px;width:117px;height:33px;background:#b9b9b9;border-radius:2px"></div>
  <div class="badge" style="left:736px;top:24px;width:24px;height:32px;background:#bdbdbd"></div>
</section>

<footer class="footer">
  <h3 style="left:252px">CLICK US</h3>
  <ul class="links">
    <li class="active">Lorem Ipsum</li><li>Lorem Ipsum</li><li>Lorem Ipsum</li><li>Lorem Ipsum</li><li>Lorem Ipsum</li>
  </ul>

  <h3 style="left:396px">CONTACT US</h3>
  <div class="address">
    <div><svg width="6" height="8" viewBox="0 0 6 9"><path d="M3 0a3 3 0 0 1 3 3c0 2-3 6-3 6S0 5 0 3a3 3 0 0 1 3-3z"/></svg><span>Lindenweg 14<br>D-61450 Falkenau</span></div>
    <div style="margin-top:2px"><svg width="8" height="6" viewBox="0 0 10 7"><path d="M0 0h10L5 4zM0 1.5l5 4 5-4V7H0z"/></svg><span>hallo@tavi-studio.de</span></div>
    <div style="margin-top:4px"><svg width="7" height="8" viewBox="0 0 10 10"><path d="M2 0l2 2-1 2c1 1.5 2 2.5 3 3l2-1 2 2-2 2C4 10 0 6 0 2z"/></svg><span>+49 1512 4411 902</span></div>
  </div>

  <div class="field" style="left:533px;top:60px;width:124px;height:18px">Ihr Name</div>
  <div class="field" style="left:533px;top:84px;width:124px;height:18px">Ihre E-Mail-Adresse</div>
  <div class="field" style="left:533px;top:109px;width:124px;height:18px">Phone number</div>
  <div class="field" style="left:664px;top:60px;width:124px;height:43px">Ihre Nachricht</div>
  <a class="btn send" href="#">SENDEN</a>

  <h3 style="left:861px">FOLLOW US</h3>
  <div class="follow"><span>Pinnwald</span><span>Kontaktor</span><span>ZOLP</span></div>
  <div class="foot-brand">
    <div class="brand-name">TAVI<span class="brand-dot"></span></div>
    <div class="brand-tag">Training · Coaching · Consulting</div>
  </div>

  <div class="copyright">Copyright © 2015 tavi-studio.de</div>
</footer>

</body>
</html>
```